Larkspur Talent IT Recruiting firm needs a business card design for Recruiters, Sourcers, and Account

We need business cards that allow us to change all contact info, names, titles (Recruiter, Sourcer, Account Manager, Director, CEO, etc) per person since we have three offices, in three cities, Phoenix, Austin, and Las Vegas. We do recruiting and contractors for IT positions (Developers, Architects, Software Engineers, Security Engineers, Help Desk, DBAs, PMs, Scrum Masters, etc.) Our client companies are very diverse from Meridian 100 to silicone Valley type start-ups.

So, while we what hip, techie, and quirky, it still needs to be professional. Primary color we use is blue, with silver as a secondary color.

Target Market(s)

IT, Technology

Industry/Entity Type

Business

Contact Information for Business Card

Company name: Larkspur Talent, Inc.
Website: www.larkspurtalent.example
Logos for Careerloop, Blipster, and Myriada

Name, Title, Office Number, Cell Number, email

Font styles to use
Serif
Sans Serif

Colors
0455a3
d5d5d5

Requirements
Nice to have
• The grey I selected below is not necessary - but, would like silver included. I included a card design (File 3: LTI early trial example.jpg) that I had started on. It's very rough, and not quite what we're looking for, but what we did like is the logo, big, maybe a bit faded, off center, goes out of frame, etc. Still looking for other ideas - you are the pros! But, just an idea of a design element we liked.

```html
<!DOCTYPE html>
<html lang="en">
<head>
<meta charset="utf-8">
<title>Larkspur Talent — Business Cards</title>
<link rel="stylesheet" href="https://fonts.googleapis.com/css2?family=Cinzel:wght@400;700&display=swap">
<style>
  :root {
    --page: #ececec;
    --card: #ffffff;
    --ink: #1c1c1c;
    --blue: #0455a3;
    --blue-light: #2aa6e4;
    --silver: #d5d5d5;
    --serif: "Cinzel", "Times New Roman", serif;
  }
  * { box-sizing: border-box; margin: 0; padding: 0; }
  html, body { width: 1200px; height: 900px; overflow: hidden; }
  body { background: var(--page); font-family: var(--serif); color: var(--ink); position: relative; }

  .card {
    position: absolute; left: 250px; width: 700px; height: 400px;
    background: var(--card); overflow: hidden;
    box-shadow: 0 6px 18px rgba(0,0,0,.18);
  }
  .card--front { top: 36px; }
  .card--back { top: 464px; }

  .brand-mark {
    position: absolute; border-radius: 50%;
    background: linear-gradient(160deg, var(--blue-light) 0%, #1e7fd0 55%, var(--blue) 100%);
    opacity: .9;
  }
  .card--front .brand-mark { width: 320px; height: 320px; right: -70px; top: 10px; }
  .card--back .brand-mark { width: 260px; height: 260px; right: 20px; top: -20px; }

  .lockup { position: absolute; display: flex; align-items: center; gap: 14px; }
  .lockup__dot {
    width: 54px; height: 54px; border-radius: 50%;
    background: linear-gradient(160deg, var(--blue-light), var(--blue));
  }
  .lockup__name { font-weight: 400; color: var(--ink); line-height: 1; letter-spacing: 3px; }
  .lockup__name span { display: block; }
  .lockup__name .big { font-size: 40px; }
  .lockup__name .small { font-size: 24px; letter-spacing: 8px; margin-top: 4px; }
  .card--front .lockup { left: 44px; top: 112px; }
  .card--back .lockup { left: 60px; top: 234px; }

  .tagline { position: absolute; font-size: 15px; letter-spacing: 3px; text-transform: uppercase; }
  .card--front .tagline { left: 60px; top: 210px; }
  .card--back .tagline { left: 64px; top: 340px; }

  .website { position: absolute; left: 330px; top: 350px; font-size: 11px; letter-spacing: 2px; text-transform: uppercase; }

  .person { position: absolute; left: 60px; top: 70px; }
  .person__name { font-size: 16px; font-weight: 700; letter-spacing: 1px; text-transform: uppercase; }
  .person__title { display: block; text-align: right; font-size: 9px; color: var(--blue); letter-spacing: 1px; text-transform: uppercase; }

  .contacts { position: absolute; left: 60px; top: 130px; list-style: none; }
  .contacts li { display: flex; align-items: center; gap: 12px; font-size: 11px; letter-spacing: .5px; text-transform: uppercase; height: 19px; }
  .contacts svg { width: 11px; height: 11px; fill: none; stroke: var(--blue); stroke-width: 1.6; }

  .socials { position: absolute; left: 430px; top: 286px; list-style: none; }
  .socials li { display: flex; align-items: center; gap: 8px; font-size: 10px; letter-spacing: 1px; text-transform: uppercase; height: 24px; }
  .socials .chip { width: 16px; height: 16px; background: var(--blue); flex: none; }
  .socials .network { color: var(--blue); }
</style>
</head>
<body>

<section class="card card--front" aria-label="Business card front">
  <div class="brand-mark" role="img" aria-label="Large brand mark running off the card edge"></div>
  <div class="lockup">
    <div class="lockup__dot"></div>
    <div class="lockup__name"><span class="big">LARKSPUR</span><span class="small">TALENT</span></div>
  </div>
  <p class="tagline">Cultivating Tech Talent</p>
  <p class="website">www.larkspurtalent.example</p>
</section>

<section class="card card--back" aria-label="Business card back">
  <div class="brand-mark" role="img" aria-label="Large brand mark running off the card edge"></div>
  <div class="person">
    <p class="person__name">Marcus D. Ellery</p>
    <span class="person__title">Director</span>
  </div>
  <ul class="contacts">
    <li><svg viewBox="0 0 12 12"><rect x="3" y="1" width="6" height="10" rx="1"/></svg>555-010-0201</li>
    <li><svg viewBox="0 0 12 12"><path d="M3 1l2 2-1 2c1 2 2 3 3 3l1-1 2 2-1 2C5 11 1 7 1 3z"/></svg>555-010-0200</li>
    <li><svg viewBox="0 0 12 12"><circle cx="6" cy="6" r="5"/><path d="M1 6h10M6 1c-3 3-3 7 0 10M6 1c3 3 3 7 0 10"/></svg>www.larkspurtalent.example</li>
    <li><svg viewBox="0 0 12 12"><rect x="1" y="2.5" width="10" height="7"/><path d="M1 2.5l5 4 5-4"/></svg>marcusd.ellery@larkspurtalent.example</li>
  </ul>
  <ul class="socials">
    <li><span class="chip"></span><span class="network">Myriada</span> Marcus D. Ellery</li>
    <li><span class="chip"></span><span class="network">Blipster</span> Marcus D. Ellery</li>
    <li><span class="chip"></span><span class="network">Careerloop</span> Marcus D. Ellery</li>
  </ul>
  <div class="lockup">
    <div class="lockup__dot"></div>
    <div class="lockup__name"><span class="big">LARKSPUR</span><span class="small">TALENT</span></div>
  </div>
  <p class="tagline">Cultivating Tech Talent</p>
</section>

</body>
</html>
```